[Design ONLY] Design for our Ecommerce business website

We require a web design for our ecommerce business website. We sell textbooks, Computer & Accessories, Gifts and stationery and Laptop/IT support service etc
Requirement:
We Require 3 pages for each design: Homepage, Product page and Payment page
Design Approach:
Design UI to be have a modern and professional feel and user experience must be good.
Responsive web design approach.
1. Home page
- Logo/Heading
- Navigation links to other pages eg. About us
- Appropriate images/banners
- A special offer
- Recent News
Include an overview of the business:
- provide general information
- contact information
- links to social media
- Frequently Asked Questions (FAQ) page
Publish store policies and make sure they are not too difficult to find:
- shipping and return policies
- outline the return process and what products can be returned
- provide easy access to a privacy policy that covers shoppers’ personal and financial information (this is crucial)
2. Product
Product Pages should include:
- Pictures, descriptions, order and price information for your products and/or services.
- Navigation links to other pages, especially home, about us, order and other product pages.
- Links to a shopping cart
- Add to wishlist
- Related or recommend products
3. Payment
- Standard payment form with payment integration with Quello and Vendrix.
- Shipping or Self Collection fee
User Experience Aspect:
Well-Defined Product Categories
a. The top level of navigation should show the set of categories that the site offers. Group products into categories and subcategories. Category labels work best as single words that describe the range of products, so shoppers can scan through them and instantly understand what they represent.
Product Search
a. Build a search function that helps them easily find what they are looking for.
Make search omnipresent: Put the search box on every page and in familiar locations. The box should be visible, quickly recognizable, and easy to use.
b. Allow sorting and filtering of results: Let shoppers sort search results based on various criteria (best sellers, highest or lowest price, product rating, newest item, etc.) as well as eliminate items that do not fit within a certain category.
Product Quick view
a. A “quick view” reduces the time it takes for shoppers to find the right product by eliminating unnecessary page loads. Also, be sure to include a prominently positioned “Add to Cart” button as well as a “Save to Wishlist” functionality.
b. Show Related and Recommended Products. This can be displayed on a product detail page.
Target Market(s)
university students
Number of Pages Required
3 page
Requirements
Must have
- Note * its a university store. not a normal ecommerce shop*
Do include design for the 3 pages specified. Homepage, product page and payment page.

```html
<!DOCTYPE html>
<html lang="en">
<head>
<meta charset="utf-8">
<title>Kampus Coop – Payment Method</title>
<link href="https://fonts.googleapis.com/css2?family=Poppins:wght@300;400;500;600;700;800&display=swap" rel="stylesheet">
<style>
:root{
  --navy:#1c2657;
  --ink:#1e2b5c;
  --footer:#1a56a6;
  --text:#555a66;
  --muted:#8a8f99;
  --line:#d9dbe0;
  --panel:#f5f6f7;
  --red:#e8403a;
  --star:#f6a623;
  --white:#fff;
}
*{box-sizing:border-box;margin:0;padding:0}
html,body{width:1200px;height:1001px;overflow:hidden;background:var(--white)}
body{font-family:'Poppins',sans-serif;color:var(--text)}
.board{position:absolute;left:0;top:0;width:2100px;height:1752px;transform:scale(.5714);transform-origin:0 0}
.a{position:absolute;white-space:nowrap}
.page-title{left:0;width:2100px;top:24px;text-align:center;font-size:38px;font-weight:500;color:var(--ink)}
.step-title{font-size:58px;font-weight:800;color:var(--ink)}
.screen{position:absolute;width:1078px;height:1385px;background:var(--white);overflow:hidden}
.topbar{left:0;top:0;width:100%;height:38px;background:var(--navy);color:var(--white);font-size:11px;font-weight:600}
.topbar .a{top:12px}
.topbar .sep{top:9px;width:1px;height:20px;background:#56608a}
.ico-c{width:16px;height:16px;border:1.5px solid #c5c9dd;border-radius:50%;top:11px !important}
.brand{font-weight:500;color:var(--navy);line-height:.95}
.search-sel{left:371px;top:63px;width:112px;height:36px;border:1px solid var(--line);font-size:11px;color:var(--muted);padding:10px 10px}
.search-in{left:483px;top:63px;width:372px;height:36px;border:1px solid var(--line)}
.badge-n{width:14px;height:14px;border-radius:50%;background:var(--navy);color:#fff;font-size:9px;text-align:center;line-height:14px}
.nav{top:120px;font-size:12px;font-weight:600;color:#111}
.nav-rule{left:0;top:145px;width:100%;height:1px;background:var(--line)}
.stepper-line{left:323px;top:175px;width:437px;height:1px;background:#999}
.dot{top:168px;width:15px;height:15px;border-radius:50%;border:1px solid #888;background:#fff}
.dot.on{background:var(--navy);border-color:var(--navy)}
.step-lbl{top:189px;font-size:15px;color:var(--muted);transform:translateX(-50%)}
.h-sec{font-size:18px;font-weight:500;color:var(--ink)}
.sub{font-size:13px;color:var(--text)}
.field{border:1px solid var(--line);border-radius:2px;font-size:11px;color:#444;padding:5px 9px}
.chk{width:12px;height:12px;border:1px solid #bbb}
.btn-main{background:var(--navy);color:#fff;text-align:center;font-size:21px}
.feat-ico{width:90px;height:70px}
.feat-lbl{font-size:13px;color:var(--text);text-align:center;line-height:1.2;white-space:normal;transform:translateX(-50%);width:150px}
.aside{position:absolute;width:335px;height:945px;background:var(--panel)}
.aside .thumb{left:26px;top:36px;width:47px;height:46px;background:linear-gradient(#b8bcc6,#7d8494)}
.aside .hr{left:25px;width:288px;height:1px;background:#c9ccd2}
.aside .link{font-size:13px;color:var(--ink);font-weight:500}
.aside .row{font-size:13px;color:var(--text)}
.tick{width:20px;height:14px}
.avatar{width:44px;height:44px;border-radius:50%;background:#d7dae0}
.stars{font-size:13px;color:var(--star);letter-spacing:1px}
.quote{font-size:13px;color:var(--text);line-height:15px;white-space:normal;width:300px}
.foot{left:0;width:100%;height:200px;background:var(--footer);color:#fff}
.foot .h{font-size:13px;font-weight:600;top:46px}
.foot .t{font-size:13px;line-height:17px;color:#dce6f5;top:76px;white-space:normal}
.foot .soc{font-size:10px;top:126px;color:#fff}
.foot .mail{top:120px;width:196px;height:34px;background:#fff;color:#999;font-size:11px;padding:9px 14px}
.foot .ebtn{top:120px;width:112px;height:34px;border:1px solid #fff;background:#fff;color:#222;font-size:11px;text-align:center;padding-top:9px}
.info-row{left:53px;width:574px;height:36px;border:1px solid var(--line);font-size:12px;color:#333;padding:10px 9px}
.info-row span{position:absolute;right:10px;color:var(--red)}
.tbl{border:1px solid var(--line)}
.pay-opt{font-size:11px;color:#333}
.card{font-size:10px;font-weight:600;color:var(--ink)}
</style>
</head>
<body>
<div class="board">
  <div class="a page-title">Payment Method</div>
  <div class="a step-title" style="left:440px;top:72px">Step 01</div>
  <div class="a step-title" style="left:1403px;top:240px">Step 02</div>

  <!-- Step 1 screen -->
  <section class="screen" style="left:0;top:190px">
    <div class="a topbar">
      <span class="a ico-c" style="left:52px"></span>
      <span class="a" style="left:77px">Purchase Offer</span>
      <svg class="a" style="left:181px;top:11px" width="18" height="16" viewBox="0 0 18 16"><path d="M3 2c1-1 3 2 3 3s-2 1-1 3 3 4 4 4 1-2 3-1 3 2 2 3-3 2-5 1S2 9 2 5c0-1 0-2 1-3z" fill="none" stroke="#fff" stroke-width="1.2"/></svg>
      <span class="a" style="left:207px">+000 000 0000</span>
      <span class="a" style="left:735px">ⓘ Need Help</span><span class="a sep" style="left:822px"></span>
      <span class="a" style="left:838px">My Account</span><span class="a sep" style="left:920px"></span>
      <span class="a" style="left:939px">User Account</span>
    </div>
    <div class="a brand" style="left:53px;top:58px;font-size:30px">KAMPUS<br>COOP</div>
    <div class="a search-sel">All Product <span style="float:right">⌄</span></div>
    <div class="a search-in"><svg class="a" style="right:14px;top:10px" width="15" height="15"><circle cx="6" cy="6" r="5" fill="none" stroke="#999" stroke-width="1.4"/><path d="M10 10l4 4" stroke="#999" stroke-width="1.4"/></svg></div>
    <svg class="a" style="left:886px;top:70px" width="24" height="22" viewBox="0 0 24 22"><path d="M4 9a8 8 0 0 1 15-2M20 13a8 8 0 0 1-15 2" fill="none" stroke="#222" stroke-width="1.6"/><path d="M19 2v5h-5M5 20v-5h5" fill="none" stroke="#222" stroke-width="1.6"/></svg>
    <svg class="a" style="left:930px;top:70px" width="24" height="22" viewBox="0 0 24 22"><path d="M12 20L3 11a5 5 0 0 1 9-6 5 5 0 0 1 9 6z" fill="none" stroke="#222" stroke-width="1.6"/></svg>
    <span class="a badge-n" style="left:947px;top:66px">0</span>
    <svg class="a" style="left:977px;top:70px" width="22" height="22" viewBox="0 0 22 22"><path d="M3 7h16l-1 13H4zM7 7a4 4 0 0 1 8 0" fill="none" stroke="#222" stroke-width="1.6"/></svg>
    <span class="a badge-n" style="left:994px;top:66px">0</span>
    <span class="a nav" style="left:52px">Computer &amp; Accessories</span>
    <span class="a nav" style="left:251px">Memorabilia</span>
    <span class="a nav" style="left:413px">Books</span>
    <span class="a nav" style="left:536px">Textbooks</span>
    <span class="a nav" style="left:674px">Others Servies</span>
    <span class="a nav" style="left:837px">About Us</span>
    <span class="a nav" style="left:948px">Kampus Coop</span>
    <div class="a nav-rule"></div>
    <div class="a stepper-line"></div>
    <span class="a dot on" style="left:388px"></span><span class="a dot" style="left:530px"></span><span class="a dot" style="left:673px"></span>
    <span class="a step-lbl" style="left:396px">Step1</span><span class="a step-lbl" style="left:538px">Step2</span><span class="a step-lbl" style="left:678px">Order Complete</span>

    <div class="a h-sec" style="left:94px;top:270px">SHIPPING INFORMATION</div>
    <div class="a sub" style="left:95px;top:294px">Field marked with *are mandotry</div>
    <div class="a field" style="left:97px;top:320px;width:525px;height:40px">Email</div>
    <span class="a chk" style="left:97px;top:376px"></span><span class="a sub" style="left:116px;top:373px">Create an Account?</span>
    <div class="a field" style="left:97px;top:402px;width:257px;height:40px">First Name</div>
    <div class="a field" style="left:367px;top:402px;width:255px;height:40px">Last Name</div>
    <div class="a field" style="left:97px;top:455px;width:257px;height:40px">Street Adress</div>
    <div class="a field" style="left:367px;top:455px;width:255px;height:40px">Town/City(optional)</div>
    <div class="a field" style="left:97px;top:507px;width:167px;height:42px">Postcode/zip</div>
    <div class="a field" style="left:276px;top:507px;width:167px;height:42px">Country<span style="float:right;margin-top:12px">▾</span></div>
    <div class="a h-sec" style="left:97px;top:570px">SHIPPING METHOD</div>
    <div class="a sub" style="left:97px;top:602px">Available Shipping Mehtod</div>
    <div class="a field" style="left:97px;top:624px;width:525px;height:34px;font-size:13px;padding-top:8px">Falt Rate<span style="float:right">$000.00</span></div>
    <div class="a h-sec" style="left:106px;top:676px">Billing Address</div>
    <span class="a chk" style="left:106px;top:707px;font-size:10px;line-height:10px;text-align:center;color:var(--navy)">✓</span>
    <span class="a sub" style="left:121px;top:704px">Use a Different billing address</span>
    <div class="a field" style="left:107px;top:730px;width:218px;height:35px;padding-top:10px">Street Address (optinal)</div>
    <div class="a field" style="left:335px;top:730px;width:218px;height:35px;padding-top:10px">Street Address (optinal)</div>
    <div class="a field" style="left:107px;top:775px;width:141px;height:34px;padding-top:10px">Post code/zip</div>
    <div class="a field" style="left:258px;top:775px;width:142px;height:34px;line-height:12px;padding-top:4px">Country (optional)<br>Singapore</div>
    <div class="a btn-main" style="left:97px;top:848px;width:525px;height:57px;padding-top:14px">CONTINUE TO PAYMENT METHOD</div>

    <svg class="a feat-ico" style="left:136px;top:960px" viewBox="0 0 90 70" role="img" aria-label="Privacy shield icon"><path d="M45 2l26 9v20c0 17-12 30-26 36C31 61 19 48 19 31V11z" fill="var(--navy)"/><rect x="37" y="31" width="16" height="13" rx="2" fill="#fff"/><path d="M40 31v-4a5 5 0 0 1 10 0v4" fill="none" stroke="#fff" stroke-width="3"/></svg>
    <svg class="a feat-ico" style="left:316px;top:960px" viewBox="0 0 90 70" role="img" aria-label="Satisfaction badge icon"><path d="M30 44l-8 22 10-5 6 8 6-16M60 44l8 22-10-5-6 8-6-16" fill="var(--navy)"/><circle cx="45" cy="30" r="26" fill="var(--navy)"/><path d="M33 30l9 9 16-17" fill="none" stroke="#fff" stroke-width="5"/></svg>
    <svg class="a feat-ico" style="left:488px;top:960px" viewBox="0 0 90 70" role="img" aria-label="Secure information icon"><rect x="3" y="4" width="84" height="54" fill="none" stroke="var(--navy)" stroke-width="4"/><rect x="3" y="4" width="84" height="10" fill="var(--navy)"/><rect x="12" y="24" width="14" height="22" fill="none" stroke="var(--navy)" stroke-width="4"/><rect x="46" y="38" width="24" height="26" fill="var(--navy)"/><path d="M50 38v-6a8 8 0 0 1 16 0v6" fill="none" stroke="var(--navy)" stroke-width="4"/><circle cx="58" cy="50" r="3" fill="#fff"/></svg>
    <div class="a feat-lbl" style="left:183px;top:1040px">We Protects Your Privacy</div>
    <div class="a feat-lbl" style="left:361px;top:1043px">100% Satisfaction Guaranteed</div>
    <div class="a feat-lbl" style="left:533px;top:1042px">Your Information is Secure</div>

    <aside class="aside" style="left:645px;top:242px">
      <div class="a thumb" role="img" aria-label="Laptop product thumbnail"></div>
      <span class="a badge-n" style="left:63px;top:32px">1</span>
      <span class="a row" style="left:88px;top:35px;color:var(--ink)">Lorem ipsum dolor sit</span>
      <span class="a row" style="right:15px;top:36px">$000.00</span>
      <div class="a hr" style="top:98px"></div>
      <span class="a link" style="left:25px;top:120px">Have a Coupon ? Click here to enter you code</span>
      <div class="a hr" style="top:156px"></div>
      <span class="a row" style="left:25px;top:172px">Subtotal</span><span class="a row" style="right:17px;top:172px">$00.00</span>
      <span class="a row" style="left:25px;top:192px">Shipping</span><span class="a row" style="right:17px;top:190px">$0.00</span>
      <div class="a hr" style="top:225px"></div>
      <span class="a" style="left:25px;top:234px;font-size:13px;font-weight:600;color:#111">Total</span>
      <span class="a" style="right:21px;top:229px;font-size:21px;font-weight:600;color:var(--ink)">$13.67</span>
      <span class="a h-sec" style="left:25px;top:282px;font-size:17px">WHY BUY FROM US</span>
      <svg class="a tick" style="left:26px;top:318px"><path d="M2 7l5 5L18 2" fill="none" stroke="var(--navy)" stroke-width="3"/></svg><span class="a row" style="left:62px;top:316px">100% Safe and secure shopping</span>
      <svg class="a tick" style="left:26px;top:351px"><path d="M2 7l5 5L18 2" fill="none" stroke="var(--navy)" stroke-width="3"/></svg><span class="a row" style="left:62px;top:349px">Best Pries</span>
      <svg class="a tick" style="left:26px;top:381px"><path d="M2 7l5 5L18 2" fill="none" stroke="var(--navy)" stroke-width="3"/></svg><span class="a row" style="left:62px;top:381px">Fast Shipping</span>
      <svg class="a tick" style="left:26px;top:414px"><path d="M2 7l5 5L18 2" fill="none" stroke="var(--navy)" stroke-width="3"/></svg><span class="a row" style="left:62px;top:413px">Quick Order Processing And Tracking</span>
      <span class="a h-sec" style="left:25px;top:458px;font-size:17px">WHAT THEY'RE SAYING</span>
      <div class="a avatar" role="img" aria-label="Customer avatar" style="left:26px;top:490px"></div>
      <span class="a row" style="left:80px;top:491px;color:#111;font-weight:500">Testumonial#1</span>
      <span class="a stars" style="left:82px;top:511px">★★★★★</span>
      <span class="a quote" style="left:25px;top:538px">Lorem ipsum dolor sit amet, consectetur adipi-scing elit, sed do eiusmod tempor</span>
      <span class="a row" style="left:25px;top:583px">Christine Mcvegihh - May 26'2020</span>
      <span class="a row" style="left:25px;top:600px">Syore Owen</span>
      <div class="a avatar" role="img" aria-label="Customer avatar" style="left:26px;top:632px"></div>
      <span class="a stars" style="left:82px;top:653px">★★★★★</span>
      <span class="a quote" style="left:25px;top:679px">Lorem ipsum dolor sit amet, consectetur adipi-scing elit, sed do eiusmod tempor</span>
      <span class="a row" style="left:25px;top:724px">Christine Mcvegihh - May 26'2020</span>
      <span class="a row" style="left:25px;top:742px">Syore Owen</span>
      <span class="a h-sec" style="left:26px;top:800px;font-size:17px">30 DAYS REFUND POLICY</span>
      <span class="a quote" style="left:26px;top:834px;width:300px">Contrary to popular belief, Lorem Ipsum is not simply random text. It has roots in a piece of classical Latin literature from 45 BC, making it over 2000 years old. Richard Hallowell, a Latin</span>
    </aside>

    <footer class="a foot" style="top:1187px">
      <div class="a brand" style="left:63px;top:33px;font-size:30px;color:#fff">KAMPUS<br>COOP</div>
      <div class="a t" style="left:63px;top:102px;width:240px">Lorem ipsum dolor sit amet, consec tetur adipiscing elit, sed do eiusmod tempor incididunt ut labore et dolo.</div>
      <div class="a h" style="left:364px">CONNECT PEOPLE</div>
      <div class="a t" style="left:358px;width:170px">Connect with us and stay in the loop.</div>
      <span class="a soc" style="left:358px">Fabla</span><span class="a soc" style="left:394px">Chirpo</span><span class="a soc" style="left:436px">Vidzo</span><span class="a soc" style="left:474px">Snapto</span>
      <div class="a h" style="left:612px">EMAIL UPDATES</div>
      <div class="a t" style="left:612px;width:190px">Be the first to hear about our Event announcements.</div>
      <div class="a mail" style="left:610px">Enter your email id <span style="float:right;color:var(--navy)">➤</span></div>
      <div class="a h" style="left:891px">CONTACT US</div>
      <div class="a t" style="left:890px;width:170px">Question? We've got answer. Try us.</div>
      <div class="a ebtn" style="left:890px">EMAIL US</div>
    </footer>
  </section>

  <!-- Step 2 screen -->
  <section class="screen" style="left:979px;top:367px">
    <div class="a topbar">
      <span class="a ico-c" style="left:53px"></span>
      <span class="a" style="left:79px">Purchase Offer</span>
      <svg class="a" style="left:183px;top:11px" width="18" height="16" viewBox="0 0 18 16"><path d="M3 2c1-1 3 2 3 3s-2 1-1 3 3 4 4 4 1-2 3-1 3 2 2 3-3 2-5 1S2 9 2 5c0-1 0-2 1-3z" fill="none" stroke="#fff" stroke-width="1.2"/></svg>
      <span class="a" style="left:209px">+000 000 0000</span>
      <span class="a" style="left:736px">ⓘ Need Help</span><span class="a sep" style="left:824px"></span>
      <span class="a" style="left:840px">My Account</span><span class="a sep" style="left:921px"></span>
      <span class="a" style="left:941px">User Account</span>
    </div>
    <div class="a brand" style="left:54px;top:58px;font-size:30px">KAMPUS<br>COOP</div>
    <div class="a search-sel" style="left:373px">All Product <span style="float:right">⌄</span></div>
    <div class="a search-in" style="left:485px"><svg class="a" style="right:14px;top:10px" width="15" height="15"><circle cx="6" cy="6" r="5" fill="none" stroke="#999" stroke-width="1.4"/><path d="M10 10l4 4" stroke="#999" stroke-width="1.4"/></svg></div>
    <svg class="a" style="left:887px;top:70px" width="24" height="22" viewBox="0 0 24 22"><path d="M4 9a8 8 0 0 1 15-2M20 13a8 8 0 0 1-15 2" fill="none" stroke="#222" stroke-width="1.6"/><path d="M19 2v5h-5M5 20v-5h5" fill="none" stroke="#222" stroke-width="1.6"/></svg>
    <svg class="a" style="left:931px;top:70px" width="24" height="22" viewBox="0 0 24 22"><path d="M12 20L3 11a5 5 0 0 1 9-6 5 5 0 0 1 9 6z" fill="none" stroke="#222" stroke-width="1.6"/></svg>
    <span class="a badge-n" style="left:948px;top:66px">0</span>
    <svg class="a" style="left:978px;top:70px" width="22" height="22" viewBox="0 0 22 22"><path d="M3 7h16l-1 13H4zM7 7a4 4 0 0 1 8 0" fill="none" stroke="#222" stroke-width="1.6"/></svg>
    <span class="a badge-n" style="left:995px;top:66px">0</span>
    <span class="a nav" style="left:53px">Computer &amp; Accessories</span>
    <span class="a nav" style="left:253px">Memorabilia</span>
    <span class="a nav" style="left:415px">Books</span>
    <span class="a nav" style="left:538px">Textbooks</span>
    <span class="a nav" style="left:676px">Others Servies</span>
    <span class="a nav" style="left:839px">About Us</span>
    <span class="a nav" style="left:950px">Kampus Coop</span>
    <div class="a nav-rule"></div>
    <div class="a stepper-line" style="left:325px"></div>
    <span class="a dot on" style="left:390px"></span><span class="a dot on" style="left:532px"></span><span class="a dot" style="left:675px"></span>
    <span class="a step-lbl" style="left:397px">Step1</span><span class="a step-lbl" style="left:539px">Step2</span><span class="a step-lbl" style="left:680px">Order Complete</span>

    <div class="a sub" style="left:53px;top:235px;color:#222">Returning customer? <span style="color:var(--red)">Click here to login</span></div>
    <div class="a info-row" style="top:273px">Email<span>Change</span></div>
    <div class="a info-row" style="top:308px">Name<span>Change</span></div>
    <div class="a info-row" style="top:344px">Ship To<span>Change</span></div>
    <div class="a info-row" style="top:380px">Method<span>Change</span></div>
    <div class="a h-sec" style="left:53px;top:435px">YOUR PRODUCT</div>
    <div class="a" style="left:56px;top:467px;font-size:11px;color:#333">Products</div>
    <div class="a tbl" style="left:45px;top:492px;width:582px;height:174px"></div>
    <div class="a" style="left:299px;top:492px;width:1px;height:174px;background:var(--line)"></div>
    <div class="a" style="left:469px;top:492px;width:1px;height:174px;background:var(--line)"></div>
    <div class="a" style="left:549px;top:492px;width:1px;height:174px;background:var(--line)"></div>
    <span class="a" style="left:64px;top:500px;font-size:12px;font-weight:600;color:#111">Nova Book Studio</span>
    <span class="a" style="left:339px;top:500px;font-size:12px;font-weight:600;color:#111">Delivery Estimate</span>
    <span class="a" style="left:496px;top:500px;font-size:12px;font-weight:600;color:#111">Qty</span>
    <span class="a" style="left:571px;top:501px;font-size:12px;font-weight:600;color:#111">Price</span>
    <div class="a" role="img" aria-label="Laptop product photo" style="left:63px;top:548px;width:52px;height:37px;background:linear-gradient(#3b4766,#1e2435)"></div>
    <span class="a quote" style="left:129px;top:543px;width:160px;font-size:12px;line-height:14px">Lorem ipsum dolor sit amet, consectetur adipi-scing elit, sed do eiusmod tempor incididunt ut</span>
    <span class="a quote" style="left:339px;top:553px;width:120px;font-size:12px;line-height:14px">Lorem ipsum dolor sit amet, consec</span>
    <span class="a" style="left:505px;top:566px;font-size:12px;color:#333">1</span>
    <span class="a" style="left:572px;top:562px;font-size:12px;color:#111">$0.00</span>
    <div class="a" style="left:67px;top:619px;width:80px;height:20px;background:var(--navy);color:#fff;font-size:11px;text-align:center;padding-top:3px">Edit Cart</div>

    <div class="a h-sec" style="left:63px;top:690px">PAYMENT INFORMATION</div>
    <div class="a" style="left:63px;top:714px;font-size:11px;color:#333">All transaction are secure and encrypted. credit card information is never stored on our servers.</div>
    <div class="a tbl" style="left:63px;top:737px;width:527px;height:122px"></div>
    <span class="a" style="left:74px;top:752px;width:12px;height:12px;border:1px solid #999;border-radius:50%"><span class="a" style="left:3px;top:3px;width:4px;height:4px;border-radius:50%;background:#222"></span></span>
    <span class="a pay-opt" style="left:99px;top:750px">Cash on delivery</span>
    <span class="a pay-opt" style="left:75px;top:793px">Pay with cash upon delivery</span>
    <span class="a" style="left:74px;top:832px;width:12px;height:12px;border:1px solid #999;border-radius:50%"></span>
    <span class="a pay-opt" style="left:98px;top:831px">Credit card (Quello)</span>
    <span class="a card" style="left:208px;top:832px">Veltra</span>
    <span class="a card" style="left:257px;top:832px">Marqo</span>
    <span class="a card" style="left:306px;top:832px">Axpra</span>
    <span class="a card" style="left:358px;top:832px">Dorvan</span>
    <span class="a card" style="left:412px;top:832px">Vendrix</span>
    <div class="a btn-main" style="left:126px;top:879px;width:402px;height:50px;font-size:22px;font-weight:700;padding-top:9px">Complete Order Now</div>

    <svg class="a feat-ico" style="left:113px;top:982px" viewBox="0 0 90 70" role="img" aria-label="Privacy shield icon"><path d="M45 2l26 9v20c0 17-12 30-26 36C31 61 19 48 19 31V11z" fill="var(--navy)"/><rect x="37" y="31" width="16" height="13" rx="2" fill="#fff"/><path d="M40 31v-4a5 5 0 0 1 10 0v4" fill="none" stroke="#fff" stroke-width="3"/></svg>
    <svg class="a feat-ico" style="left:291px;top:982px" viewBox="0 0 90 70" role="img" aria-label="Satisfaction badge icon"><path d="M30 44l-8 22 10-5 6 8 6-16M60 44l8 22-10-5-6 8-6-16" fill="var(--navy)"/><circle cx="45" cy="30" r="26" fill="var(--navy)"/><path d="M33 30l9 9 16-17" fill="none" stroke="#fff" stroke-width="5"/></svg>
    <svg class="a feat-ico" style="left:464px;top:982px" viewBox="0 0 90 70" role="img" aria-label="Secure information icon"><rect x="3" y="4" width="84" height="54" fill="none" stroke="var(--navy)" stroke-width="4"/><rect x="3" y="4" width="84" height="10" fill="var(--navy)"/><rect x="12" y="24" width="14" height="22" fill="none" stroke="var(--navy)" stroke-width="4"/><rect x="46" y="38" width="24" height="26" fill="var(--navy)"/><path d="M50 38v-6a8 8 0 0 1 16 0v6" fill="none" stroke="var(--navy)" stroke-width="4"/><circle cx="58" cy="50" r="3" fill="#fff"/></svg>
    <div class="a feat-lbl" style="left:159px;top:1062px">We Protects Your Privacy</div>
    <div class="a feat-lbl" style="left:336px;top:1065px">100% Satisfaction Guaranteed</div>
    <div class="a feat-lbl" style="left:509px;top:1064px">Your Information is Secure</div>

    <aside class="aside" style="left:647px;top:241px;width:364px">
      <div class="a thumb" role="img" aria-label="Laptop product thumbnail"></div>
      <span class="a badge-n" style="left:63px;top:32px">1</span>
      <span class="a row" style="left:88px;top:35px;color:var(--ink)">Lorem ipsum dolor sit</span>
      <span class="a row" style="right:45px;top:36px">$000.00</span>
      <div class="a hr" style="top:98px"></div>
      <span class="a link" style="left:25px;top:120px">Have a Coupon ? Click here to enter you code</span>
      <div class="a hr" style="top:156px"></div>
      <span class="a row" style="left:25px;top:172px">Subtotal</span><span class="a row" style="right:47px;top:172px">$00.00</span>
      <span class="a row" style="left:25px;top:192px">Shipping</span><span class="a row" style="right:47px;top:190px">$0.00</span>
      <div class="a hr" style="top:225px"></div>
      <span class="a" style="left:25px;top:234px;font-size:13px;font-weight:600;color:#111">Total</span>
      <span class="a" style="right:47px;top:229px;font-size:21px;font-weight:600;color:var(--ink)">$00.00</span>
      <span class="a h-sec" style="left:25px;top:282px;font-size:17px">WHY BUY FROM US</span>
      <svg class="a tick" style="left:26px;top:318px"><path d="M2 7l5 5L18 2" fill="none" stroke="var(--navy)" stroke-width="3"/></svg><span class="a row" style="left:62px;top:316px">100% Safe and secure shopping</span>
      <svg class="a tick" style="left:26px;top:351px"><path d="M2 7l5 5L18 2" fill="none" stroke="var(--navy)" stroke-width="3"/></svg><span class="a row" style="left:62px;top:349px">Best Pries</span>
      <svg class="a tick" style="left:26px;top:381px"><path d="M2 7l5 5L18 2" fill="none" stroke="var(--navy)" stroke-width="3"/></svg><span class="a row" style="left:62px;top:381px">Fast Shipping</span>
      <svg class="a tick" style="left:26px;top:414px"><path d="M2 7l5 5L18 2" fill="none" stroke="var(--navy)" stroke-width="3"/></svg><span class="a row" style="left:62px;top:413px">Quick Order Processing And Tracking</span>
      <span class="a h-sec" style="left:25px;top:458px;font-size:17px">WHAT THEY'RE SAYING</span>
      <div class="a avatar" role="img" aria-label="Customer avatar" style="left:26px;top:490px"></div>
      <span class="a row" style="left:80px;top:491px;color:#111;font-weight:500">Testumonial#1</span>
      <span class="a stars" style="left:82px;top:511px">★★★★★</span>
      <span class="a quote" style="left:25px;top:538px">Lorem ipsum dolor sit amet, consectetur adipi-scing elit, sed do eiusmod tempor</span>
      <span class="a row" style="left:25px;top:583px">Christine Mcvegihh - May 26'2020</span>
      <span class="a row" style="left:25px;top:600px">Syore Owen</span>
      <div class="a avatar" role="img" aria-label="Customer avatar" style="left:26px;top:632px"></div>
      <span class="a stars" style="left:82px;top:653px">★★★★★</span>
      <span class="a quote" style="left:25px;top:679px">Lorem ipsum dolor sit amet, consectetur adipi-scing elit, sed do eiusmod tempor</span>
      <span class="a row" style="left:25px;top:724px">Christine Mcvegihh - May 26'2020</span>
      <span class="a row" style="left:25px;top:742px">Syore Owen</span>
      <span class="a h-sec" style="left:26px;top:800px;font-size:17px">30 DAYS REFUND POLICY</span>
      <span class="a quote" style="left:26px;top:834px;width:300px">Contrary to popular belief, Lorem Ipsum is not simply random text. It has roots in a piece of classical Latin literature from 45 BC, making it over 2000 years old. Richard Hallowell, a Latin</span>
    </aside>

    <footer class="a foot" style="top:1186px">
      <div class="a brand" style="left:64px;top:33px;font-size:30px;color:#fff">KAMPUS<br>COOP</div>
      <div class="a t" style="left:64px;top:102px;width:240px">Lorem ipsum dolor sit amet, consec tetur adipiscing elit, sed do eiusmod tempor incididunt ut labore et dolo.</div>
      <div class="a h" style="left:366px">CONNECT PEOPLE</div>
      <div class="a t" style="left:360px;width:170px">Connect with us and stay in the loop.</div>
      <span class="a soc" style="left:360px">Fabla</span><span class="a soc" style="left:396px">Chirpo</span><span class="a soc" style="left:438px">Vidzo</span><span class="a soc" style="left:476px">Snapto</span>
      <div class="a h" style="left:613px">EMAIL UPDATES</div>
      <div class="a t" style="left:613px;width:190px">Be the first to hear about our Event announcements.</div>
      <div class="a mail" style="left:612px">Enter your email id <span style="float:right;color:var(--navy)">➤</span></div>
      <div class="a h" style="left:893px">CONTACT US</div>
      <div class="a t" style="left:892px;width:170px">Question? We've got answer. Try us.</div>
      <div class="a ebtn" style="left:892px">EMAIL US</div>
      <div class="a" style="left:1046px;top:55px;width:32px;height:64px;background:var(--navy)">
        <svg class="a" style="left:8px;top:9px" width="16" height="14"><path d="M1 1h14v9H6l-4 3V10H1z" fill="#fff"/></svg>
        <svg class="a" style="left:8px;top:41px" width="16" height="12"><rect x="1" y="1" width="14" height="10" fill="#fff"/><path d="M1 1l7 6 7-6" fill="none" stroke="var(--navy)" stroke-width="1.3"/></svg>
      </div>
    </footer>
  </section>
</div>
</body>
</html>
```